Vorn upkeep KT Solar Venture

Solar power system install
Services and maintenance
wiring, Rewinding and Renovation
Switch Board Upgrade
Power and lighting point
t doesn’t matter how much you spend on quality parts, your solar system will let you down if your design and installation are sub-par. Have your solar system tailored and installed by our Master Electrician and Bright Grid Guild Accredited team.

Target Market(s)

sales and installed

Industry/Entity Type

Solar install and retailer

Contact Information for Business Card

Name , Email, Phone Number ,Business address,

Font styles to use
Serif

Colors
0054AA
0677BA
7BADD7
CADEEF
E8F1F8

Requirements
Must have
• clear and bright
Nice to have
• new design
Should not have
• unclear pictures

```html
<!DOCTYPE html>
<html lang="en">
<head>
<meta charset="utf-8">
<title>Vorn upkeep – Business Card</title>
<link href="https://fonts.googleapis.com/css2?family=Roboto+Slab:wght@400;500;700&display=swap" rel="stylesheet">
<style>
  :root {
    --backdrop: #2c2c2d;
    --card: #f1f1f1;
    --card-shade: #e6e6e6;
    --brand-blue: #0a5aa8;
    --brand-green: #1b8a3c;
    --band-green: #5aa33a;
    --band-blue: #0677ba;
    --ink: #1e1e1e;
    --icon-green: #1f8a3a;
    --band-text: #eaf4e6;
  }
  * { margin: 0; padding: 0; box-sizing: border-box; }
  html, body {
    width: 1200px; height: 1138px; overflow: hidden;
    background: var(--backdrop);
    font-family: "Roboto Slab", Georgia, serif;
  }
  .card {
    position: absolute;
    width: 623px; height: 376px;
    border-radius: 16px;
    background: linear-gradient(180deg, var(--card) 0%, #f5f5f5 50%, var(--card-shade) 100%);
    overflow: hidden;
  }
  .card--front { left: 274px; top: 186px; }
  .card--back { left: 276px; top: 608px; }

  .brand {
    position: absolute;
    display: flex; align-items: center;
    font-weight: 700;
    text-transform: uppercase;
    white-space: nowrap;
  }
  .brand__dot { flex: none; border-radius: 50%; background: var(--brand-blue); }
  .brand__text { display: flex; flex-direction: column; }
  .brand__name { color: var(--brand-blue); line-height: 1; }
  .brand__tagline { color: var(--brand-green); line-height: 1; }

  .card--front .brand { left: 98px; top: 52px; gap: 14px; }
  .card--front .brand__dot { width: 124px; height: 124px; }
  .card--front .brand__name { font-size: 33px; letter-spacing: -0.3px; }
  .card--front .brand__tagline { font-size: 28px; letter-spacing: 3.2px; margin-top: 8px; }

  .services {
    position: absolute; left: 0; top: 239px;
    width: 100%; height: 74px;
    background: linear-gradient(90deg, var(--band-green) 0%, #3f9a58 35%, var(--band-blue) 75%, #0670b4 100%);
    color: var(--band-text);
    font-size: 15px;
    text-align: center;
    display: flex; flex-direction: column; justify-content: center; gap: 6px;
    white-space: nowrap;
  }
  .website {
    position: absolute; left: 0; top: 333px; width: 100%;
    display: flex; align-items: center; justify-content: center; gap: 26px;
    font-size: 15px; color: var(--ink);
  }
  .website__rule { width: 80px; height: 2px; }
  .website__rule--blue { background: linear-gradient(90deg, transparent, var(--band-blue)); }
  .website__rule--green { background: linear-gradient(90deg, var(--band-green), transparent); }

  .contact { position: absolute; left: 60px; top: 86px; color: var(--ink); white-space: nowrap; }
  .contact__name { font-size: 23px; font-weight: 700; color: var(--brand-blue); }
  .contact__role { font-size: 15px; margin-top: 4px; }
  .contact__address { font-size: 15px; line-height: 24px; margin-top: 30px; }
  .contact__list { list-style: none; margin-top: 6px; }
  .contact__list li {
    display: flex; align-items: center; gap: 16px;
    font-size: 15px; line-height: 24px;
  }
  .contact__list svg { width: 16px; height: 16px; fill: var(--icon-green); }

  .card--back .brand { left: 318px; top: 76px; flex-direction: column; gap: 20px; }
  .card--back .brand__dot { width: 128px; height: 128px; }
  .card--back .brand__text { align-items: center; }
  .card--back .brand__name { font-size: 27px; letter-spacing: -0.3px; }
  .card--back .brand__tagline { font-size: 23px; letter-spacing: 2.6px; margin-top: 7px; }
</style>
</head>
<body>

<section class="card card--front">
  <div class="brand">
    <span class="brand__dot"></span>
    <span class="brand__text">
      <span class="brand__name">Vorn upkeep</span>
      <span class="brand__tagline">Solar Venture</span>
    </span>
  </div>
  <div class="services">
    <p>Solar Power System Install &nbsp;|&nbsp; Wiring, Rewinding &amp; Renovation</p>
    <p>Services &amp; Maintenance &nbsp;|&nbsp; Switch Board Upgrade &nbsp;|&nbsp; Power &amp; Lighting Point</p>
  </div>
  <div class="website">
    <span class="website__rule website__rule--blue"></span>
    <span>www.ktsolarventure.com</span>
    <span class="website__rule website__rule--green"></span>
  </div>
</section>

<section class="card card--back">
  <div class="contact">
    <h1 class="contact__name">Marlo Teaven Quill</h1>
    <p class="contact__role">Managing Director</p>
    <p class="contact__address">58 Brindle Row, Harlow Vale,<br>Fenmark, US 407219</p>
    <ul class="contact__list">
      <li>
        <svg viewBox="0 0 16 16" aria-hidden="true"><path d="M2 5c0-2 2-3 6-3s6 1 6 3v1h-3V5H5v1H2zM4 7h8l2 7H2zm4 1.5a2.5 2.5 0 1 0 0 5 2.5 2.5 0 0 0 0-5z"/></svg>
        <span>555-204-7316</span>
      </li>
      <li>
        <svg viewBox="0 0 16 16" aria-hidden="true"><path d="M1 3h14v10H1zm1.5 1.5v.4L8 9l5.5-4.1v-.4zm0 2.2v4.8h11V6.7L8 10.8z"/></svg>
        <span>marlo@ktsolarventure.com</span>
      </li>
      <li>
        <svg viewBox="0 0 16 16" aria-hidden="true"><path d="M8 1a7 7 0 1 0 0 14A7 7 0 0 0 8 1zm-1 2.2V5H4.6A5 5 0 0 1 7 3.2zm2 0A5 5 0 0 1 11.4 5H9zM3.2 7H7v2H3.2a5 5 0 0 1 0-2zM9 7h3.8a5 5 0 0 1 0 2H9zm-4.4 4H7v1.8A5 5 0 0 1 4.6 11zM9 11h2.4A5 5 0 0 1 9 12.8z"/></svg>
        <span>www.ktsolarventure.com</span>
      </li>
    </ul>
  </div>
  <div class="brand">
    <span class="brand__dot"></span>
    <span class="brand__text">
      <span class="brand__name">Vorn upkeep</span>
      <span class="brand__tagline">Solar Venture</span>
    </span>
  </div>
</section>

</body>
</html>
```